Vorelan.com Personal Trainer/Fitness Website

I want a website to market my personal training/Outdoor Bootcamp Class services, as well as to ditribute nutrivex. I need a logo as well I included an address for the Harbor Gales 1975 logo. I'd like Vorelan in place of Harbor Gales, and in Black and white, just different enough so I can't get sued by the PBL.
https://www.pictofind.example/imgres?imgurl=http%3A%2F%2Fwww.darnell-quibury.example%2Fwp-content%2Fuploads%2F2014%2F01%2Fgales_logo4.jpg&imgrefurl=http%3A%2F%2Fwww.darnell-quibury.example%2Fpbl-logo-redesigns-harbor-gales%2F&docid=_qkwzR7TBAgXpL&tbnid=m4tpU8KdOXjnRP%3A&w=600&h=450&client=ms-android-carrier&bih=512&biw=360&ved=0ahUKEwiRtpgyp9HMAhUTwGMKHRPMBWMQMwg6KBQwFA&iact=mrc&uact=8.
It should be about 5 pages 1. home 2. about 3. Services 4. Blog/Videos and programs 5. Contact.
http://www.dorvinfitness.example.uk/ is a website I like the style of.

Target Market(s)

Seattle area

Industry/Entity Type

Fitness

Coding

Coded - Design and coding required

Number of Pages Required

4 page

Font styles to use
Serif
Sans Serif

Requirements
Must have
• A minimal look
Nice to have
• A logo similar to the 1975 Harbor Galewinds Logo, with a Small Milo Brandt ripping his shirt open(with a picture of the logo on his shirt, picture within picture) to turn into Ironjaw in the center. Skyline is black, Background and small figure white(with black logo on shirt)

```html
<!DOCTYPE html>
<html lang="en">
<head>
<meta charset="utf-8">
<title>Vorelan – Personal Training &amp; Bootcamp</title>
<link href="https://fonts.googleapis.com/css2?family=Lato:wght@300;400;700;900&display=swap" rel="stylesheet">
<style>
:root{
  --black:#0d0d0d;
  --ink:#1b1b1b;
  --dark:#2a2a2a;
  --slate:#3d3d3d;
  --mid:#6a6a6a;
  --light:#e9e9e9;
  --white:#ffffff;
  --accent:#f39a3c;
  --green:#9bd34a;
  --red:#d8433a;
  --blue:#2d79c4;
  --sky:#3fb1e4;
}
*{margin:0;padding:0;box-sizing:border-box}
html,body{width:1200px;height:3284px;overflow:hidden}
body{font-family:"Lato",Arial,sans-serif;color:var(--ink);background:var(--white);position:relative}
.abs{position:absolute}
.btn{display:inline-block;background:var(--black);color:var(--white);font-weight:700;font-size:13px;letter-spacing:1px;padding:11px 22px;text-transform:uppercase}

/* header */
.topbar{top:0;left:0;width:1200px;height:136px;background:var(--white)}
.brand{left:80px;top:30px;display:flex;align-items:center;gap:14px}
.brand-mark{width:72px;height:72px;border-radius:50%;background:var(--black)}
.brand-name{font-size:36px;font-weight:900;color:var(--black);letter-spacing:1px}
.member{right:90px;top:12px;font-size:13px;padding:10px 20px;display:flex;align-items:center;gap:8px}
.contact-row{right:90px;top:70px;display:flex;align-items:center;gap:10px;font-size:17px;font-weight:700}
.social{display:flex;gap:8px;margin-left:10px}
.social span{width:28px;height:28px;border-radius:50%;display:block}
.nav{top:136px;left:0;width:1200px;height:40px;background:var(--black);display:flex;justify-content:space-between;padding:0 80px}
.nav a{color:var(--white);text-decoration:none;font-size:13px;font-weight:700;letter-spacing:1px;line-height:40px;padding:0 22px}
.nav a.active{background:var(--slate)}

/* hero */
.hero{top:176px;left:0;width:1200px;height:614px;background:linear-gradient(160deg,#9aa58a 0%,#6f7d5c 35%,#4e5a45 65%,#8d8c88 100%)}
.hero-copy{right:90px;top:74px;text-align:left;width:420px}
.hero-kicker{color:var(--accent);font-size:26px;font-weight:400;letter-spacing:1px}
.hero-title{color:var(--white);font-size:44px;font-weight:900;line-height:1.1;margin:6px 0 26px}

/* offers */
.offers{top:790px;left:0;width:1200px;height:190px;background:var(--slate)}
.offer{top:40px;width:330px;text-align:center;color:var(--white)}
.offer h3{font-size:22px;font-weight:700;margin-bottom:18px}
.offer .btn{background:var(--ink);border:1px solid #555}
.signup{top:760px;left:410px;width:380px;height:220px;background:var(--ink);text-align:center;color:var(--white);padding-top:38px;box-shadow:0 0 18px rgba(0,0,0,.5)}
.signup .s1{font-size:28px;font-weight:700}
.signup .s2{font-size:38px;font-weight:900;color:var(--green);margin:6px 0 20px}
.signup .s3{font-size:24px;font-weight:900;letter-spacing:1px}

/* services */
.services{top:980px;left:0;width:1200px;height:508px;background:linear-gradient(180deg,#505050,#3b3b3b);color:var(--white);text-align:center}
.sec-title{font-size:32px;font-weight:900;letter-spacing:1px;padding-top:52px}
.rule{width:60px;height:3px;background:var(--white);margin:12px auto 18px}
.lead{width:600px;margin:0 auto;font-size:13px;line-height:1.6;color:#ddd}
.svc-row{display:flex;justify-content:space-between;width:1040px;margin:40px auto 0}
.svc{width:230px}
.svc-icon{width:84px;height:84px;border-radius:50%;background:var(--ink);border:3px solid var(--white);margin:0 auto 22px;display:flex;align-items:center;justify-content:center}
.svc h4{font-size:18px;font-weight:700;margin-bottom:10px}
.svc p{font-size:12px;line-height:1.6;color:#ddd}
.arrow-btn{width:24px;height:20px;background:var(--white);margin:16px auto 0;display:flex;align-items:center;justify-content:center}

/* welcome */
.welcome{top:1488px;left:0;width:1200px;height:292px;text-align:center}
.welcome h2{font-size:34px;font-weight:900;padding-top:46px;display:flex;justify-content:center;align-items:center;gap:14px}
.welcome h2 i{width:36px;height:36px;border-radius:50%;background:var(--black);display:block}
.welcome p{width:900px;margin:20px auto 22px;font-size:13px;line-height:1.6;color:#444}

/* amenities */
.amenities{top:1780px;left:0;width:1200px;height:420px;background:var(--black)}
.am-left{left:0;top:0;width:520px;height:420px;background:linear-gradient(135deg,#87a3c0,#6e8a6a 60%,#a38363)}
.am-right{right:0;top:0;width:480px;height:420px;background:linear-gradient(135deg,#9a9a9a,#4f4f4f 60%,#cfcfcf)}
.am-panel{left:400px;top:0;width:420px;height:420px;background:var(--ink);clip-path:polygon(22% 0,100% 0,78% 100%,0 100%)}
.am-copy{left:480px;top:70px;width:260px;color:var(--white);text-align:center}
.am-copy h3{font-size:28px;font-weight:900;line-height:1.15}
.am-copy h3 span{font-size:40px;display:block}
.am-copy p{font-size:15px;font-weight:700;line-height:1.5;margin:22px 0}
.play{left:140px;top:180px}

/* feature cards */
.card{top:2240px;width:320px;height:184px;background:linear-gradient(160deg,#8a8a8a,#474747);color:var(--white);text-align:center;padding-top:52px}
.card h4{font-size:20px;font-weight:700;margin-top:14px}

/* events */
.events{top:2480px;left:0;width:1200px;height:300px;background:var(--black)}
.ev-photo{left:0;top:0;width:600px;height:300px;background:linear-gradient(120deg,#c9b8a8,#7f8f6c 50%,#5b6a50)}
.ev-copy{left:640px;top:56px;width:470px;color:var(--white)}
.ev-copy h3{font-size:30px;font-weight:700;line-height:1.25}
.ev-copy p{font-size:12px;line-height:1.6;color:#ccc;margin:18px 0 20px}
.ev-copy .btn{background:var(--dark)}

/* footer */
.footer{top:2780px;left:0;width:1200px;height:452px;background:#1c1c1c;color:var(--white)}
.news{left:72px;top:36px;width:640px;height:68px;background:var(--dark);display:flex;align-items:center;gap:14px;padding:0 18px;font-size:17px}
.news .field{width:300px;height:32px;background:var(--white);color:#777;font-size:12px;line-height:32px;padding-left:10px}
.news .btn{padding:9px 14px;font-size:12px}
.follow{left:760px;top:56px;display:flex;align-items:center;gap:12px;font-size:17px;font-weight:700}
.follow span{width:30px;height:30px;border-radius:50%;border:2px solid #aaa;display:block}
.fcol{top:136px}
.fcol h4{font-size:24px;font-weight:700;margin-bottom:20px;display:flex;align-items:center;gap:10px}
.form{display:grid;grid-template-columns:230px 230px;gap:12px 20px}
.form label{font-size:12px;color:#ccc;display:block;margin-bottom:6px}
.form .inp{height:30px;background:var(--white)}
.form .msg{grid-row:span 2;height:100px;background:var(--white)}
.form .btn{width:230px;text-align:center;background:var(--dark);padding:8px}
.links li{list-style:none;font-size:14px;line-height:1.85;color:#ddd}
.links li::before{content:"› ";color:#999}
.info{font-size:13px;line-height:1.6;color:#ddd}
.info div{display:flex;gap:10px;margin-bottom:12px}
.copyright{top:3232px;left:0;width:1200px;height:52px;background:var(--black);color:#bbb;font-size:12px;text-align:center;line-height:52px;letter-spacing:1px}
</style>
</head>
<body>

<header>
  <div class="abs topbar"></div>
  <div class="abs brand"><span class="brand-mark"></span><span class="brand-name">VORELAN</span></div>
  <a class="abs btn member"><svg width="14" height="14" viewBox="0 0 14 14"><circle cx="7" cy="4" r="3" fill="#fff"/><path d="M1 14c0-4 3-6 6-6s6 2 6 6z" fill="#fff"/></svg>Become a Member</a>
  <div class="abs contact-row">
    <svg width="20" height="20" viewBox="0 0 20 20"><circle cx="10" cy="10" r="9" fill="none" stroke="#1b1b1b" stroke-width="2"/><path d="M7 5l2 2-1 2c1 2 2 3 3 3l2-1 2 2-2 2c-4 0-8-4-8-8z" fill="#1b1b1b"/></svg>
    123-456-7890
    <div class="social"><span style="background:var(--red)"></span><span style="background:var(--blue)"></span><span style="background:var(--sky)"></span><span style="background:var(--red)"></span></div>
  </div>
  <nav class="abs nav">
    <a class="active">HOME</a><a>ABOUT</a><a>SERVICES</a><a>BLOG</a><a>VIDEOS</a><a>PROGRAMS</a><a>CONTACT</a>
  </nav>
</header>

<section class="abs hero" role="img" aria-label="Outdoor bootcamp class doing sit-ups on grass in a park with a trainer standing over them">
  <div class="abs hero-copy">
    <div class="hero-kicker">GET FIT AND HAVE FUN</div>
    <div class="hero-title">THE WAY IT SHOULD BE</div>
    <a class="btn">Get Started</a>
  </div>
</section>

<section class="abs offers">
  <div class="abs offer" style="left:70px"><h3>Get Access To All Facilites</h3><a class="btn">Subscribe Now</a></div>
  <div class="abs offer" style="left:800px"><h3>Offer Free Consultation</h3><a class="btn">Get Consultation</a></div>
</section>
<div class="abs signup">
  <div class="s1">Signup For 6 Month</div>
  <div class="s2">Get 30% off</div>
  <div class="s3">SIGN UP!</div>
</div>

<section class="abs services">
  <h2 class="sec-title">OUR SERVICES</h2>
  <div class="rule"></div>
  <p class="lead">Lorem ipsum dolor sit amet, consectetur adipiscing elit. Morbi quis ante sed massa consectetur feugiat id at tellus. Fusce tristique dictum tincidunt, from viverra euismod pulvinar.</p>
  <div class="svc-row">
    <div class="svc">
      <div class="svc-icon"><svg width="44" height="44" viewBox="0 0 44 44"><rect x="4" y="14" width="6" height="16" fill="#fff"/><rect x="34" y="14" width="6" height="16" fill="#fff"/><rect x="10" y="18" width="4" height="8" fill="#fff"/><rect x="30" y="18" width="4" height="8" fill="#fff"/><rect x="14" y="20" width="16" height="4" fill="#fff"/></svg></div>
      <h4>Personal Training</h4>
      <p>Lorem ipsum dolor sit amet, consectetur adipiscing elit, sed diam.</p>
      <div class="arrow-btn"><svg width="8" height="10" viewBox="0 0 8 10"><path d="M0 0l8 5-8 5z" fill="#111"/></svg></div>
    </div>
    <div class="svc">
      <div class="svc-icon"><svg width="44" height="44" viewBox="0 0 44 44"><circle cx="22" cy="24" r="14" fill="none" stroke="#fff" stroke-width="3"/><rect x="19" y="4" width="6" height="5" fill="#fff"/><path d="M22 24V15" stroke="#fff" stroke-width="3"/></svg></div>
      <h4>Outdoor Bootcamp Classes</h4>
      <p>Lorem ipsum dolor sit amet, consectetur adipiscing elit, sed diam.</p>
      <div class="arrow-btn"><svg width="8" height="10" viewBox="0 0 8 10"><path d="M0 0l8 5-8 5z" fill="#111"/></svg></div>
    </div>
    <div class="svc">
      <div class="svc-icon"><svg width="44" height="44" viewBox="0 0 44 44"><circle cx="12" cy="14" r="4" fill="#fff"/><circle cx="22" cy="11" r="5" fill="#fff"/><circle cx="32" cy="14" r="4" fill="#fff"/><path d="M5 32c0-6 3-10 7-10s7 4 7 10zM14 34c0-8 4-12 8-12s8 4 8 12zM25 32c0-6 3-10 7-10s7 4 7 10z" fill="#fff"/></svg></div>
      <h4>Outdoor Group Training</h4>
      <p>Lorem ipsum dolor sit amet, consectetur adipiscing elit, sed diam.</p>
      <div class="arrow-btn"><svg width="8" height="10" viewBox="0 0 8 10"><path d="M0 0l8 5-8 5z" fill="#111"/></svg></div>
    </div>
    <div class="svc">
      <div class="svc-icon"><svg width="44" height="44" viewBox="0 0 44 44"><rect x="5" y="8" width="34" height="22" rx="2" fill="none" stroke="#fff" stroke-width="3"/><rect x="18" y="30" width="8" height="5" fill="#fff"/><rect x="12" y="35" width="20" height="3" fill="#fff"/></svg></div>
      <h4>Online Coaching</h4>
      <p>Lorem ipsum dolor sit amet, consectetur adipiscing elit, sed diam.</p>
      <div class="arrow-btn"><svg width="8" height="10" viewBox="0 0 8 10"><path d="M0 0l8 5-8 5z" fill="#111"/></svg></div>
    </div>
  </div>
</section>

<section class="abs welcome">
  <h2><i></i>WELCOME TO VORELAN</h2>
  <p>Lorem ipsum dolor sit amet, consectetur adipiscing elit, sed diam nonummy nibh euismod tincidunt ut laoreet dolore magna aliquam erat volutpat. Ut wisi enim ad minim veniam, quis nostrud exerci tation ullamcorper suscipit lobortis nisl ut aliquip ex ea commodo consequat. Duis autem vel eum iriure dolor in hendrerit in vulputate velit esse molestie consequat, vel illum dolore eu feugiat nulla facilisis.</p>
  <a class="btn" style="font-size:11px;padding:7px 14px">Read More</a>
</section>

<section class="abs amenities">
  <div class="abs am-left" role="img" aria-label="Group doing push-ups outdoors during a bootcamp session"></div>
  <svg class="abs play" width="80" height="80" viewBox="0 0 80 80"><circle cx="40" cy="40" r="36" fill="rgba(0,0,0,.35)" stroke="#fff" stroke-width="3"/><path d="M32 24l22 16-22 16z" fill="#fff"/></svg>
  <div class="abs am-right" role="img" aria-label="Black and white gym interior with rows of treadmills"></div>
  <div class="abs am-panel"></div>
  <div class="abs am-copy">
    <h3>STATE OF THE ART <span>AMENITIES</span></h3>
    <p>FEATURING THE BEST EQUIPMENT, LOCKER ROOMS, SMOOTHIE BAR &amp; MORE.</p>
    <a class="btn" style="background:var(--slate)">Learn More</a>
  </div>
</section>

<div class="abs card" style="left:80px" role="img" aria-label="Consultation meeting backdrop">
  <svg width="48" height="40" viewBox="0 0 48 40"><circle cx="12" cy="8" r="5" fill="#fff"/><circle cx="36" cy="8" r="5" fill="#fff"/><path d="M4 28c0-8 4-12 8-12s8 4 8 12zM28 28c0-8 4-12 8-12s8 4 8 12z" fill="#fff"/><rect x="8" y="30" width="32" height="4" fill="#fff"/></svg>
  <h4>Free Consultation</h4>
</div>
<div class="abs card" style="left:440px" role="img" aria-label="Healthy food backdrop">
  <svg width="40" height="40" viewBox="0 0 40 40"><circle cx="20" cy="24" r="14" fill="#fff"/><path d="M20 10c0-4 3-7 7-8" stroke="#fff" stroke-width="3" fill="none"/></svg>
  <h4>Nutrition Guidance</h4>
</div>
<div class="abs card" style="left:800px;padding-top:40px" role="img" aria-label="Trainer in the gym backdrop">
  <svg width="48" height="40" viewBox="0 0 48 40"><circle cx="24" cy="8" r="6" fill="#fff"/><path d="M12 36c0-10 5-16 12-16s12 6 12 16z" fill="#fff"/><rect x="2" y="24" width="10" height="4" fill="#fff"/><rect x="36" y="24" width="10" height="4" fill="#fff"/></svg>
  <h4>Get A<br>Personal Trainer</h4>
</div>

<section class="abs events">
  <div class="abs ev-photo" role="img" aria-label="Smiling group of women training together outdoors"></div>
  <div class="abs ev-copy">
    <h3>We Organize &amp; Participate<br>In Group Events</h3>
    <p>Lorem ipsum dolor sit amet, consectetur adipiscing elit, sed diam nonummy nibh euismod tincidunt ut laoreet dolore magna aliquam erat volutpat enim ad minim.</p>
    <a class="btn">Learn More</a>
  </div>
</section>

<footer class="abs footer">
  <div class="abs news">
    <svg width="22" height="16" viewBox="0 0 22 16"><rect x="1" y="1" width="20" height="14" fill="none" stroke="#fff" stroke-width="2"/><path d="M1 1l10 8 10-8" fill="none" stroke="#fff" stroke-width="2"/></svg>
    Newsletter Signup
    <span class="field">Enter your email here</span>
    <a class="btn">Subscribe</a>
  </div>
  <div class="abs follow">Follow Us <span></span><span></span><span></span><span></span></div>

  <div class="abs fcol" style="left:80px">
    <h4><svg width="22" height="22" viewBox="0 0 22 22"><circle cx="11" cy="11" r="9" fill="none" stroke="#fff" stroke-width="2"/><path d="M11 10v6" stroke="#fff" stroke-width="2"/><circle cx="11" cy="6.5" r="1.3" fill="#fff"/></svg>QUICK INQUIRY</h4>
    <div class="form">
      <div><label>Name</label><div class="inp"></div></div>
      <div style="grid-row:span 2"><label>Message</label><div class="msg"></div></div>
      <div><label>Email Address</label><div class="inp"></div></div>
      <div><label>Phone Number</label><div class="inp"></div></div>
      <div style="align-self:end"><a class="btn">Submit</a></div>
    </div>
  </div>

  <div class="abs fcol" style="left:620px">
    <h4><svg width="20" height="20" viewBox="0 0 20 20"><path d="M8 12l4-4M6 9l-2 2a3 3 0 004 4l2-2M14 11l2-2a3 3 0 00-4-4l-2 2" stroke="#fff" stroke-width="2" fill="none"/></svg>Quick Links</h4>
    <ul class="links"><li>Home</li><li>About</li><li>Services</li><li>Blog</li><li>Videos</li><li>Programs</li><li>Contact</li></ul>
  </div>

  <div class="abs fcol" style="left:850px;width:270px">
    <h4><svg width="20" height="20" viewBox="0 0 20 20"><circle cx="10" cy="10" r="9" fill="none" stroke="#fff" stroke-width="2"/><path d="M10 9v6" stroke="#fff" stroke-width="2"/><circle cx="10" cy="5.5" r="1.2" fill="#fff"/></svg>Contact Information</h4>
    <div class="info">
      <div><svg width="14" height="18" viewBox="0 0 14 18"><path d="M7 18S1 10 1 7a6 6 0 0112 0c0 3-6 11-6 11z" fill="#fff"/><circle cx="7" cy="7" r="2" fill="#1c1c1c"/></svg><span>Vorelan Fitness<br>Lorem ipsum dolor sit amet,<br>Seattle, WA 98101</span></div>
      <div><svg width="14" height="14" viewBox="0 0 20 20"><path d="M5 1l4 4-2 3c1 3 3 5 5 5l3-2 4 4-3 3C9 18 2 11 2 4z" fill="#fff"/></svg><span>123-456-7890</span></div>
      <div><svg width="16" height="12" viewBox="0 0 22 16"><rect x="1" y="1" width="20" height="14" fill="none" stroke="#fff" stroke-width="2"/><path d="M1 1l10 8 10-8" fill="none" stroke="#fff" stroke-width="2"/></svg><span>info@vorelan.com</span></div>
    </div>
  </div>
</footer>
<div class="abs copyright">COPYRIGHT 2016 VORELAN. ALL RIGHT RESERVED</div>

</body>
</html>
```